Dunmore Roofing

Want a professional looking business card

Industry/Entity Type

Business

Contact Information for Business Card

Paul Dunmore ( Owner) paul@dunmoreroofing-example.com, www.dunmoreroofing-example.com, Adress: 4172 Township road 43 Fenwick Falls,ON K9X4T2

```html
<!DOCTYPE html>
<html lang="en">
<head>
<meta charset="utf-8">
<title>Dunmore Roofing – Business Card</title>
<link rel="stylesheet" href="https://fonts.googleapis.com/css2?family=Montserrat:ital,wght@0,400;0,500;0,700;0,800;1,700&display=swap">
<style>
  :root {
    --brand-blue: #1d4a8f;
    --brand-blue-deep: #23307a;
    --brand-blue-light: #2b5596;
    --steel-grey: #8a8d92;
    --text-grey: #4a4d52;
    --card-white: #ffffff;
    --stage: #1b1c1e;
  }
  * { box-sizing: border-box; margin: 0; padding: 0; }
  html, body { width: 1200px; height: 963px; overflow: hidden; }
  body {
    background: var(--stage);
    font-family: "Montserrat", sans-serif;
    display: flex; flex-direction: column; align-items: center; justify-content: center;
    gap: 60px;
  }
  .card {
    position: relative;
    width: 640px; height: 366px;
    border-radius: 18px;
    overflow: hidden;
    box-shadow: 0 14px 40px rgba(0,0,0,.55);
  }
  /* Front */
  .card--front { background: linear-gradient(160deg, #ffffff 40%, #eef0f3 100%); }
  .contact { position: absolute; left: 44px; top: 40px; color: var(--text-grey); }
  .contact__name { color: var(--brand-blue); font-weight: 700; font-style: italic; font-size: 20px; letter-spacing: .5px; text-transform: uppercase; }
  .contact__role { font-size: 12px; letter-spacing: 1px; text-transform: uppercase; margin-top: 2px; }
  .contact__address { font-size: 12.5px; line-height: 1.5; margin-top: 18px; }
  .contact__list { list-style: none; margin-top: 16px; font-size: 12.5px; line-height: 1.75; }
  .contact__list li { display: flex; align-items: center; gap: 9px; }
  .contact__list svg { width: 12px; height: 12px; fill: var(--brand-blue); flex: none; }
  .contact__web { color: var(--brand-blue); }
  .wordmark {
    position: absolute; display: flex; align-items: center; gap: 14px;
    color: var(--brand-blue); font-weight: 800; text-transform: uppercase;
  }
  .wordmark__square { width: 22px; height: 22px; background: currentColor; flex: none; }
  .wordmark__text { display: flex; flex-direction: column; line-height: 1; }
  .wordmark__name { font-size: 40px; letter-spacing: 1px; }
  .wordmark__sub { font-size: 15px; letter-spacing: 17px; margin-top: 8px; }
  .card--front .wordmark { right: 40px; top: 170px; }
  .swoosh { position: absolute; left: 0; bottom: 0; width: 640px; height: 130px; }
  /* Back */
  .card--back { background: linear-gradient(135deg, var(--brand-blue-light) 0%, var(--brand-blue-deep) 100%); }
  .card--back .wordmark { color: #e9eaec; left: 50%; top: 120px; transform: translateX(-50%); }
  .back__web { position: absolute; left: 0; right: 0; bottom: 70px; text-align: center; color: #e9eaec; font-size: 14px; letter-spacing: .5px; }
</style>
</head>
<body>
  <section class="card card--front" aria-label="Business card front">
    <div class="contact">
      <p class="contact__name">Paul Dunmore</p>
      <p class="contact__role">Owner</p>
      <p class="contact__address">4172 Township road 43<br>Fenwick Falls, ON K9X4T2</p>
      <ul class="contact__list">
        <li><svg viewBox="0 0 24 24" aria-hidden="true"><path d="M6.6 10.8a15.1 15.1 0 0 0 6.6 6.6l2.2-2.2a1 1 0 0 1 1-.25 11.4 11.4 0 0 0 3.6.57 1 1 0 0 1 1 1V20a1 1 0 0 1-1 1A17 17 0 0 1 3 4a1 1 0 0 1 1-1h3.5a1 1 0 0 1 1 1c0 1.25.2 2.45.57 3.57a1 1 0 0 1-.25 1z"/></svg>(555)010-2468</li>
        <li><svg viewBox="0 0 24 24" aria-hidden="true"><path d="M2 5h20v14H2zm2 2v.5l8 5 8-5V7zm0 2.9V17h16V9.9l-8 5z"/></svg>paul@dunmoreroofing-example.com</li>
        <li><svg viewBox="0 0 24 24" aria-hidden="true"><path d="M12 2a10 10 0 1 0 0 20 10 10 0 0 0 0-20zm6.9 6h-3a15.7 15.7 0 0 0-1.4-4A8 8 0 0 1 18.9 8zM12 4a14 14 0 0 1 1.9 4h-3.8A14 14 0 0 1 12 4zM4.3 14a8 8 0 0 1 0-4h3.4a16.5 16.5 0 0 0 0 4zm.8 2h3a15.7 15.7 0 0 0 1.4 4A8 8 0 0 1 5.1 16zm3-8h-3a8 8 0 0 1 4.4-4 15.7 15.7 0 0 0-1.4 4zM12 20a14 14 0 0 1-1.9-4h3.8A14 14 0 0 1 12 20zm2.3-6H9.7a14.7 14.7 0 0 1 0-4h4.6a14.7 14.7 0 0 1 0 4zm.2 6a15.7 15.7 0 0 0 1.4-4h3a8 8 0 0 1-4.4 4zm1.8-6a16.5 16.5 0 0 0 0-4h3.4a8 8 0 0 1 0 4z"/></svg><span class="contact__web">www.dunmoreroofing-example.com</span></li>
      </ul>
    </div>
    <div class="wordmark">
      <span class="wordmark__square"></span>
      <span class="wordmark__text"><span class="wordmark__name">Dunmore</span><span class="wordmark__sub">Roofing</span></span>
    </div>
    <svg class="swoosh" viewBox="0 0 640 130" preserveAspectRatio="none" aria-hidden="true">
      <path d="M0 8 L300 92 Q330 100 360 102 L640 102 L640 106 L356 106 Q326 104 296 96 L0 14 Z" fill="var(--steel-grey)"/>
      <path d="M0 24 L290 104 Q318 112 350 112 Q420 112 470 118 Q520 124 640 124 L640 130 L0 130 Z" fill="var(--brand-blue)"/>
    </svg>
  </section>

  <section class="card card--back" aria-label="Business card back">
    <div class="wordmark">
      <span class="wordmark__square"></span>
      <span class="wordmark__text"><span class="wordmark__name">Dunmore</span><span class="wordmark__sub">Roofing</span></span>
    </div>
    <p class="back__web">www.dunmoreroofing-example.com</p>
  </section>
</body>
</html>
```